Kelumo.cn needs pages to be re-designed

www.kelumo.cn is our current new site which was launched in April.
We're a financial services website in the crowdfunding space in China to connect borrower's and lender's.

test.kelumo.cn is our test site
u: test
p: newtest
http://test.kelumo.cn/
http://test.kelumo.cn/user/accounts/new_lender
http://test.kelumo.cn/user/accounts/new_borrower
http://test.kelumo.cn/introductions/protection
http://test.kelumo.cn/introductions
http://test.kelumo.cn/introductions/kelumo_admin
http://test.kelumo.cn/introductions/contact
Some of the pages have pop-ups in the bloc's of the pages. Please click the links, to see more content.

User's currently criticize the website for being:
- Too Western looking
- Too simple, too little content
- Content NOT in the pop-ups are too simple
- Pictures are too big and too much blank space
- Relevant information is not there when needed
- The pictures are too generic

What we would like to do is re-design those pages with the same color scheme and style to be more compelling, efficient, non-intimidating and easy-to-use. Our audience is Ages 25-35 predominantly male investors.
We are looking for more ideas to make the content match the style, while bridging western and chinese design. Our ultimate goal is to increase registrants to the website and highlight our core competitive advantages.

Some competitors websites are:
www.fobuxiqi.com
www.tamev.com
www.zzzlendo.com

Reason: Not enough good designs that follow the prompt. Same style, better information layout!

Reason: Still have not received a design we're satisfied with

Reason: WE DONT WANT A COMPLETE REDESIGN OF PAGES . KEEP THE EXACT SAME COLOR AND STYLE - WE WANT CONTENT RE-DESIGN! THE BLOCS ARE TOO SIMPLE - WE WANT MORE CONTENT INSIDE.

Reason: no new designs

Reason: no new designs

Reason: other non-registered pages need to be re-designed

```html
<!DOCTYPE html>
<html lang="zh-CN">
<head>
<meta charset="utf-8">
<title>Kelumo — 关于我们</title>
<link rel="stylesheet" href="https://fonts.googleapis.com/css2?family=Noto+Sans+SC:wght@400;500;700&display=swap">
<style>
:root{
  --green:#6ab42d;
  --green-dark:#4f9420;
  --green-light:#a7d47c;
  --green-pale:#dcefc9;
  --ink:#3a3a3a;
  --text:#555;
  --muted:#8a8a8a;
  --line:#d6d6d6;
  --band:#f1f2f1;
  --bar:#363636;
  --footer:#3b3b3b;
  --footer-text:#bdbdbd;
  --white:#fff;
}
*{box-sizing:border-box;margin:0;padding:0}
html,body{width:1200px;height:3479px;overflow:hidden}
body{font-family:"Noto Sans SC",sans-serif;color:var(--text);background:var(--white);position:relative;font-size:13px}
.abs{position:absolute}

/* header */
.site-header{top:0;left:0;width:1200px;height:73px;background:var(--white);border-bottom:1px solid #e6e6e6}
.brand{left:105px;top:17px;display:flex;align-items:center;gap:10px}
.brand-dot{width:38px;height:38px;border-radius:50%;background:var(--green)}
.brand-name{font-size:22px;font-weight:700;color:var(--green)}
.main-nav{right:100px;top:0;height:73px;display:flex;gap:38px;align-items:center}
.main-nav a{color:var(--ink);text-decoration:none;font-size:14px;display:flex;align-items:center;gap:6px}
.main-nav a.active{color:var(--green);font-weight:500}
.main-nav svg{width:16px;height:16px}

/* hero */
.hero{top:73px;left:0;width:1200px;height:497px;background:linear-gradient(100deg,#cfd6dc 0%,#eef1f3 35%,#fbfbfb 60%,#e4e8ea 100%)}

/* tab bar */
.feature-bar{top:570px;left:0;width:1200px;height:62px;background:var(--bar);display:flex;justify-content:center;gap:0}
.feature-bar .tab{width:200px;display:flex;align-items:center;justify-content:center;gap:10px;color:var(--white);font-size:20px;border-right:1px solid #4a4a4a}
.feature-bar .tab:last-child{border-right:none}
.feature-bar svg{width:26px;height:26px}

/* section titles */
.section-title{left:0;width:1200px;text-align:center;font-size:22px;color:var(--ink)}
.section-title::after{content:"";display:block;width:40px;height:2px;background:var(--green);margin:10px auto 0}

.diagram{top:720px;left:0;width:1200px;height:700px}
.diagram text{font-family:"Noto Sans SC",sans-serif}

/* feature cards */
.feature-band{top:1440px;left:0;width:1200px;height:1160px;background:var(--band)}
.card{width:470px;height:360px}
.card-head{display:flex;align-items:center;gap:10px;height:44px;border-bottom:1px solid var(--line);position:relative}
.card-head::after{content:"";position:absolute;left:0;bottom:-1px;width:70px;height:2px;background:var(--green)}
.card-icon{width:34px;height:34px;border-radius:50%;background:var(--green);display:flex;align-items:center;justify-content:center}
.card-icon svg{width:18px;height:18px}
.card-title{font-size:21px;color:var(--ink)}
.card-sub{font-size:14px;font-weight:700;color:var(--ink);margin-top:22px}
.card-copy{font-size:11px;line-height:19px;color:var(--muted);width:210px;margin-top:8px}
.card svg.art{position:absolute}
.more-btn{display:inline-block;margin-top:12px;padding:4px 14px;background:var(--green);color:var(--white);font-size:11px;border-radius:2px}

.data-table{position:absolute;border-collapse:collapse;font-size:11px;color:var(--text)}
.data-table th{font-weight:500;background:#e3e3e3;padding:5px 10px;text-align:left}
.data-table td{padding:5px 10px;border-bottom:1px solid #e3e3e3}

/* safety box */
.safety{top:2640px;left:130px;width:940px;height:270px;border:2px solid var(--green);border-radius:6px;background:var(--white)}
.safety-head{top:-24px;left:370px;width:200px;background:var(--white);display:flex;align-items:center;justify-content:center;gap:10px;font-size:22px;color:var(--ink)}
.safety-col{top:40px;width:440px;height:200px}
.safety-label{top:95px;font-size:20px;color:var(--ink);border-bottom:2px solid var(--green);padding-bottom:4px}
.safety-list{list-style:none;left:190px;top:0}
.safety-list li{font-size:12px;line-height:25px;color:var(--text);padding-left:16px;position:relative}
.safety-list li::before{content:"";position:absolute;left:0;top:8px;border-left:8px solid var(--green);border-top:5px solid transparent;border-bottom:5px solid transparent}
.safety-link{left:190px;top:165px;font-size:12px;color:var(--green);border-bottom:1px solid var(--green)}

.cta{top:2985px;left:490px;width:220px;height:52px;border-radius:26px;background:var(--green);color:var(--white);font-size:20px;display:flex;align-items:center;justify-content:center;gap:10px}
.cta-ring{width:28px;height:28px;border-radius:50%;border:2px solid var(--white);display:flex;align-items:center;justify-content:center}

/* partners */
.partners{top:3060px;left:0;width:1200px;height:135px;background:#fafafa;border-top:1px solid #eee}
.partners-label{left:110px;top:14px;font-size:12px;color:var(--ink)}
.partner-row{left:110px;top:52px;display:flex;gap:26px;align-items:center}
.partner-name{font-size:13px;font-weight:700;color:#6d6d6d;display:flex;align-items:center;gap:6px}
.partner-name i{width:12px;height:12px;background:#bbb;display:block}

/* footer */
.site-footer{top:3195px;left:0;width:1200px;height:284px;background:var(--footer);color:var(--footer-text)}
.footer-links{left:110px;top:28px;font-size:12px;line-height:26px}
.footer-links span{margin-right:14px}
.hotline{right:110px;top:22px;text-align:right}
.hotline small{font-size:12px;display:block}
.hotline strong{font-size:30px;color:var(--white);font-weight:500;letter-spacing:1px}
.hotline em{font-style:normal;font-size:11px;display:block}
.service-row{left:110px;top:110px;display:flex;gap:8px;align-items:center;font-size:12px}
.service-row i{width:22px;height:22px;border-radius:50%;background:#5a5a5a;display:block}
.service-row .pill{padding:3px 12px;border:1px solid #777;border-radius:12px;margin-left:20px}
.badges{left:360px;top:170px;display:flex;gap:14px}
.badges i{width:100px;height:34px;background:#e8e8e8;border-radius:2px;display:block}
.copyright{left:0;width:1200px;top:240px;text-align:center;font-size:11px;color:#8e8e8e}
.footer-brand{right:110px;top:232px;display:flex;gap:6px;align-items:center;font-size:14px;color:var(--white);font-weight:700}
.footer-brand i{width:20px;height:20px;border-radius:50%;background:var(--green);display:block}
</style>
</head>
<body>

<header class="site-header abs">
  <div class="brand abs"><span class="brand-dot"></span><span class="brand-name">Kelumo</span></div>
  <nav class="main-nav abs">
    <a href="#"><svg viewBox="0 0 16 16"><path d="M2 8 8 2l6 6v6H10V10H6v4H2z" fill="#888"/></svg>首页</a>
    <a href="#" class="active"><svg viewBox="0 0 16 16"><circle cx="8" cy="8" r="7" fill="#6ab42d"/></svg>关于</a>
    <a href="#"><svg viewBox="0 0 16 16"><rect x="2" y="4" width="12" height="9" rx="1" fill="#888"/></svg>借款</a>
    <a href="#"><svg viewBox="0 0 16 16"><rect x="3" y="2" width="10" height="12" rx="1" fill="#888"/></svg>投资</a>
    <a href="#"><svg viewBox="0 0 16 16"><circle cx="8" cy="5" r="3" fill="#888"/><path d="M2 15c0-4 3-6 6-6s6 2 6 6z" fill="#888"/></svg>登录 ▾</a>
  </nav>
</header>

<div class="hero abs" role="img" aria-label="手握钢笔在纸上绘制灯泡、房屋与数学公式草图的照片"></div>

<div class="feature-bar abs">
  <div class="tab"><svg viewBox="0 0 26 26"><rect x="3" y="10" width="20" height="14" rx="2" fill="#fff"/><path d="M7 10V7a6 6 0 0 1 12 0v3" stroke="#fff" stroke-width="2.5" fill="none"/></svg>风控</div>
  <div class="tab"><svg viewBox="0 0 26 26"><path d="M13 2 23 6v7c0 6-5 10-10 11C8 23 3 19 3 13V6z" fill="#fff"/></svg>保护金</div>
  <div class="tab"><svg viewBox="0 0 26 26"><path d="M13 3v20M4 8h18M4 8l-3 7h6zM22 8l-3 7h6z" stroke="#fff" stroke-width="2" fill="none"/></svg>分数</div>
  <div class="tab"><svg viewBox="0 0 26 26"><circle cx="6" cy="13" r="4" fill="#fff"/><circle cx="20" cy="6" r="4" fill="#fff"/><circle cx="20" cy="20" r="4" fill="#fff"/><path d="M6 13 20 6M6 13l14 7" stroke="#fff" stroke-width="2"/></svg>资金安全</div>
  <div class="tab"><svg viewBox="0 0 26 26"><path d="M3 12h5v11H3zM10 12l5-9c2 0 3 1 3 3l-1 5h6c1 0 2 1 2 2l-2 9H10z" fill="#fff"/></svg>责任</div>
</div>

<h2 class="section-title abs" style="top:672px">6 標題範例</h2>

<svg class="diagram abs" viewBox="0 0 1200 700" aria-label="资金流向结构图">
  <defs>
    <g id="person"><circle cx="0" cy="-9" r="6" fill="#9a9a9a"/><path d="M-11 12c0-10 5-13 11-13s11 3 11 13z" fill="#9a9a9a"/></g>
    <g id="person-s"><circle cx="0" cy="-6" r="4" fill="#9a9a9a"/><path d="M-7 8c0-7 3-9 7-9s7 2 7 9z" fill="#9a9a9a"/></g>
  </defs>
  <g stroke="#6ab42d" stroke-width="2" fill="none">
    <path d="M150 40H520M680 40H920"/>
    <path d="M150 40V430H530"/>
    <path d="M920 40V90"/>
  </g>
  <text x="600" y="45" text-anchor="middle" font-size="13" fill="#6ab42d">標題範例</text>
  <use href="#person" x="205" y="150"/>
  <text x="205" y="180" text-anchor="middle" font-size="10" fill="#888">示例文本</text>
  <line x1="225" y1="140" x2="520" y2="140" stroke="#bbb"/>
  <text x="530" y="124" font-size="12" fill="#555"><tspan font-weight="700">2. 每年:</tspan> 示例文本項</text>
  <line x1="530" y1="132" x2="640" y2="132" stroke="#6ab42d" stroke-width="2"/>
  <text x="905" y="85" font-size="12" fill="#555"><tspan font-weight="700">1. 每年:</tspan> 示例文本項</text>
  <line x1="905" y1="92" x2="1000" y2="92" stroke="#6ab42d" stroke-width="2"/>
  <g stroke="#bbb">
    <path d="M985 100V320M985 130H1000M985 190H1000M985 250H1000M985 310H1000"/>
  </g>
  <use href="#person-s" x="985" y="125"/><use href="#person-s" x="985" y="185"/>
  <use href="#person-s" x="985" y="245"/><use href="#person-s" x="985" y="305"/>
  <text x="1005" y="134" font-size="10" fill="#888">示例文本</text>
  <text x="1005" y="194" font-size="10" fill="#888">示例文本</text>
  <text x="1005" y="254" font-size="10" fill="#888">示例文本</text>
  <text x="1005" y="314" font-size="10" fill="#888">示例文本</text>
  <line x1="150" y1="333" x2="990" y2="333" stroke="#6ab42d" stroke-width="2"/>
  <rect x="565" y="323" width="80" height="20" fill="#fff"/>
  <text x="605" y="338" text-anchor="middle" font-size="13" fill="#555">標題範例</text>
  <g stroke="#bbb"><path d="M515 345V600M515 420H525M515 490H525"/></g>
  <text x="530" y="424" font-size="12" fill="#555"><tspan font-weight="700">3. 每年:</tspan> 標題範例標題範例</text>
  <text x="530" y="494" font-size="12" fill="#555"><tspan font-weight="700">4. 每年:</tspan> 標題範例標題範例標題範例</text>
  <line x1="530" y1="502" x2="760" y2="502" stroke="#6ab42d" stroke-width="2"/>
  <circle cx="800" cy="488" r="14" fill="#6ab42d"/>
  <text x="800" y="520" text-anchor="middle" font-size="11" fill="#555">安信保险</text>
  <text x="840" y="493" font-size="18" fill="#555">+</text>
  <text x="865" y="494" font-size="18" font-weight="700" fill="#555">Norvale</text>
  <text x="865" y="512" font-size="10" fill="#888">诺维保险经纪</text>
  <rect x="470" y="575" width="90" height="22" fill="#3a3a3a"/>
  <text x="515" y="590" text-anchor="middle" font-size="11" fill="#fff">了解详情</text>
  <text x="367" y="660" font-size="12" fill="#555"><tspan font-weight="700">5. 每年:</tspan> 標題範例標題範例標題範例</text>
  <line x1="367" y1="668" x2="600" y2="668" stroke="#6ab42d" stroke-width="2"/>
  <text x="655" y="660" font-size="12" fill="#555"><tspan font-weight="700">6. 每年:</tspan> 標題範例標題範例標題範例</text>
  <line x1="655" y1="668" x2="900" y2="668" stroke="#6ab42d" stroke-width="2"/>
</svg>

<section class="feature-band abs">
  <!-- 1 风控 -->
  <article class="card abs" style="left:110px;top:30px">
    <div class="card-head"><span class="card-icon"><svg viewBox="0 0 18 18"><rect x="3" y="8" width="12" height="8" fill="#fff"/></svg></span><span class="card-title">1, 风控</span></div>
    <p class="card-sub">標本標題標本標題</p>
    <p class="card-copy">全面审核借款人身份信息、收入证明与信用记录，多重风控模型逐层筛选，只有符合条件的借款申请才能进入平台，从源头降低坏账风险，保障投资人资金安全与收益稳定。</p>
    <svg class="art" viewBox="0 0 220 200" style="left:245px;top:70px;width:220px;height:200px">
      <polygon points="10,0 170,0 158,26 22,26" fill="#3f7f17"/>
      <polygon points="24,30 156,30 144,56 36,56" fill="#5aa227"/>
      <polygon points="38,60 142,60 130,86 50,86" fill="#6ab42d"/>
      <polygon points="52,90 128,90 116,116 64,116" fill="#8cc65a"/>
      <polygon points="66,120 114,120 102,146 78,146" fill="#a7d47c"/>
      <polygon points="80,150 100,150 90,176" fill="#c9e5ac"/>
      <g font-size="9" fill="#888"><text x="178" y="17">示例</text><text x="164" y="47">示例</text><text x="150" y="77">示例</text><text x="136" y="107">示例</text><text x="122" y="137">示例</text></g>
    </svg>
  </article>

  <!-- 2 分数 -->
  <article class="card abs" style="left:620px;top:30px">
    <div class="card-head"><span class="card-icon"><svg viewBox="0 0 18 18"><path d="M9 2v14M3 5h12" stroke="#fff" stroke-width="2"/></svg></span><span class="card-title">2, 分数</span></div>
    <p class="card-sub">標本標題標本標題</p>
    <p class="card-copy">您的投资将被分散至多笔借款，每笔投资金额较小，即使个别借款出现逾期，整体收益也不会受到明显影响，让风险更可控。</p>
    <svg class="art" viewBox="0 0 250 300" style="left:210px;top:40px;width:250px;height:300px">
      <defs><g id="p2"><circle cx="0" cy="-6" r="5" fill="#9a9a9a"/><path d="M-9 9c0-8 4-10 9-10s9 2 9 10z" fill="#9a9a9a"/></g></defs>
      <use href="#p2" x="30" y="150"/>
      <text x="30" y="175" text-anchor="middle" font-size="9" fill="#888">示例文本</text>
      <text x="30" y="190" text-anchor="middle" font-size="10" fill="#6ab42d">¥ 1000</text>
      <path d="M45 150H80M80 20V280M80 20H110M80 85H110M80 150H110M80 215H110M80 280H110" stroke="#bbb" fill="none"/>
      <g><use href="#p2" x="125" y="20"/><use href="#p2" x="125" y="85"/><use href="#p2" x="125" y="150"/><use href="#p2" x="125" y="215"/><use href="#p2" x="125" y="280"/></g>
      <g font-size="10" fill="#6ab42d"><text x="145" y="24">¥ 200</text><text x="145" y="89">¥ 200</text><text x="145" y="154">¥ 200</text><text x="145" y="219">¥ 200</text><text x="145" y="284">¥ 200</text></g>
    </svg>
  </article>

  <!-- 3 保护金 -->
  <article class="card abs" style="left:110px;top:410px">
    <div class="card-head"><span class="card-icon"><svg viewBox="0 0 18 18"><path d="M9 1 16 4v5c0 4-3 7-7 8-4-1-7-4-7-8V4z" fill="#fff"/></svg></span><span class="card-title">3, 保护金</span></div>
    <p class="card-sub">標題範例</p>
    <p class="card-copy">平台按每笔借款金额提取一定比例作为风险保护金，专户存管，当借款逾期时用于优先偿付投资人本金。</p>
    <svg class="art" viewBox="0 0 200 120" style="left:250px;top:50px;width:200px;height:120px">
      <circle cx="55" cy="60" r="42" fill="none" stroke="#dcefc9" stroke-width="20"/>
      <circle cx="55" cy="60" r="42" fill="none" stroke="#6ab42d" stroke-width="20" stroke-dasharray="200 264" transform="rotate(-90 55 60)"/>
      <circle cx="55" cy="60" r="42" fill="none" stroke="#3f7f17" stroke-width="20" stroke-dasharray="40 264" stroke-dashoffset="-200" transform="rotate(-90 55 60)"/>
      <g font-size="9" fill="#888"><rect x="115" y="30" width="8" height="8" fill="#6ab42d"/><text x="128" y="38">示例文本</text><rect x="115" y="55" width="8" height="8" fill="#3f7f17"/><text x="128" y="63">示例文本</text><rect x="115" y="80" width="8" height="8" fill="#dcefc9"/><text x="128" y="88">示例文本</text></g>
    </svg>
    <table class="data-table" style="left:40px;top:200px">
      <tr><th>示例文本</th><th>示例文本</th><th>示例文本</th></tr>
      <tr><td>1-9天</td><td>100% 示例文本</td><td>示例文本</td></tr>
      <tr><td>10-30天</td><td>100% 示例文本</td><td>示例文本</td></tr>
      <tr><td>30天+</td><td>100% 示例文本</td><td>示例文本</td></tr>
    </table>
    <span class="more-btn abs" style="left:190px;top:315px">了解保护金制度</span>
  </article>

  <!-- 4 风险 -->
  <article class="card abs" style="left:620px;top:410px">
    <div class="card-head"><span class="card-icon"><svg viewBox="0 0 18 18"><path d="M9 1 16 4v5c0 4-3 7-7 8-4-1-7-4-7-8V4z" fill="#fff"/></svg></span><span class="card-title">4, 将您的风险</span></div>
    <p class="card-sub">每月示例文本每月示例文本</p>
    <svg class="art" viewBox="0 0 460 250" style="left:0;top:100px;width:460px;height:250px">
      <defs><g id="p4"><circle cx="0" cy="-6" r="5" fill="#9a9a9a"/><path d="M-9 9c0-8 4-10 9-10s9 2 9 10z" fill="#9a9a9a"/></g></defs>
      <g stroke="#bbb" fill="none"><path d="M60 40 230 110M60 110H230M60 180 230 110M230 110 370 30M230 110 370 80M230 110 370 140M230 110 370 200"/></g>
      <use href="#p4" x="50" y="40"/><use href="#p4" x="50" y="110"/><use href="#p4" x="50" y="180"/>
      <g font-size="9" fill="#888"><text x="30" y="65">示例文本</text><text x="30" y="135">示例文本</text><text x="30" y="205">示例文本</text></g>
      <circle cx="230" cy="110" r="24" fill="#6ab42d"/>
      <text x="230" y="150" text-anchor="middle" font-size="10" fill="#555">Kelumo</text>
      <g font-size="11" fill="#555" font-weight="700"><text x="380" y="34">Norvale</text><text x="380" y="84">安信保险</text><text x="380" y="144">汇联支付</text><text x="380" y="204">通宝支付</text></g>
    </svg>
  </article>

  <!-- 5 资金安全 -->
  <article class="card abs" style="left:110px;top:790px">
    <div class="card-head"><span class="card-icon"><svg viewBox="0 0 18 18"><rect x="3" y="7" width="12" height="9" fill="#fff"/><path d="M5 7V5a4 4 0 0 1 8 0v2" stroke="#fff" stroke-width="2" fill="none"/></svg></span><span class="card-title">5, 资金安全</span></div>
    <p class="card-sub">资金安全</p>
    <p class="card-copy">投资人资金全部由第三方支付机构托管，平台不接触用户资金，所有资金往来均在托管账户中完成，交易过程全程可查，确保资金流向透明清晰，杜绝资金池风险。</p>
    <svg class="art" viewBox="0 0 200 200" style="left:250px;top:60px;width:200px;height:200px">
      <circle cx="100" cy="20" r="7" fill="#9a9a9a"/><path d="M88 42c0-12 5-15 12-15s12 3 12 15z" fill="#9a9a9a"/>
      <path d="M100 46V70" stroke="#bbb"/>
      <rect x="40" y="72" width="120" height="26" fill="#6ab42d"/><text x="100" y="89" text-anchor="middle" font-size="10" fill="#fff">第三方托管账户</text>
      <path d="M100 98V120" stroke="#bbb"/>
      <rect x="40" y="122" width="120" height="26" fill="#8a6d4a"/><text x="100" y="139" text-anchor="middle" font-size="10" fill="#fff">示例文本示例</text>
      <path d="M100 148V170" stroke="#bbb"/>
      <rect x="60" y="172" width="80" height="20" fill="#dcefc9"/><text x="100" y="186" text-anchor="middle" font-size="9" fill="#555">示例文本</text>
    </svg>
  </article>

  <!-- 6 风险 -->
  <article class="card abs" style="left:620px;top:790px">
    <div class="card-head"><span class="card-icon"><svg viewBox="0 0 18 18"><circle cx="9" cy="9" r="6" fill="#fff"/></svg></span><span class="card-title">6, 将您的风险</span></div>
    <p class="card-sub">资金安全</p>
    <p class="card-copy">平台系统部署于专业云服务商，数据多重加密备份，交易与支付由持牌支付机构完成，资金进出均有记录，安全稳定有保障。</p>
    <div class="abs" style="left:260px;top:80px">
      <p style="font-size:20px;font-weight:700;color:#555">CloudHarbor</p>
      <p style="font-size:10px;color:#888;margin:4px 0 14px">资金托管账户</p>
      <p class="partner-name" style="margin-bottom:12px"><i></i>汇联支付</p>
      <p class="partner-name" style="margin-bottom:12px"><i></i>通宝支付</p>
      <p class="partner-name"><i></i>易安付</p>
    </div>
  </article>
</section>

<section class="safety abs">
  <div class="safety-head abs"><span class="card-icon"><svg viewBox="0 0 18 18"><circle cx="9" cy="6" r="3" fill="#fff"/><path d="M3 16c0-5 3-7 6-7s6 2 6 7z" fill="#fff"/></svg></span>资金安全</div>
  <div class="safety-col abs" style="left:40px">
    <p class="safety-label abs" style="left:30px">将您的风险</p>
    <ul class="safety-list abs">
      <li>投资资金由第三方托管账户存管</li>
      <li>借款项目均经过严格审核筛选</li>
      <li>逾期借款由保护金优先垫付本金</li>
      <li>分散投资有效降低单笔违约影响</li>
      <li>全程电子合同具备法律效力保障</li>
      <li>专业团队实时监控借款人还款</li>
    </ul>
    <a class="safety-link abs">了解详情</a>
  </div>
  <div class="safety-col abs" style="left:480px">
    <p class="safety-label abs" style="left:30px">将您的</p>
    <ul class="safety-list abs">
      <li>收益按月回款，资金灵活周转</li>
      <li>投资门槛低，百元即可起投</li>
      <li>账户信息加密存储安全可靠</li>
      <li>随时查看投资明细与回款计划</li>
      <li>客服专员一对一解答投资疑问</li>
      <li>新手专享标的，轻松开启理财</li>
    </ul>
    <a class="safety-link abs">了解详情</a>
  </div>
</section>

<a class="cta abs"><span class="cta-ring"><svg viewBox="0 0 12 12" width="12" height="12"><path d="M3 1l6 5-6 5z" fill="#fff"/></svg></span>开始投资</a>

<section class="partners abs">
  <p class="partners-label abs">合作机构</p>
  <div class="partner-row abs">
    <span class="partner-name"><i></i>Norvale</span>
    <span class="partner-name"><i></i>CloudHarbor</span>
    <span class="partner-name"><i></i>安信保险</span>
    <span class="partner-name"><i></i>汇联支付</span>
    <span class="partner-name"><i></i>通宝支付</span>
    <span class="partner-name"><i></i>易安付</span>
  </div>
</section>

<footer class="site-footer abs">
  <div class="footer-links abs">
    <p><span>首页</span><span>投资</span><span>借款</span><span>关于我们</span><span>新手指引</span><span>帮助中心</span><span>加入我们</span><span>联系方式</span></p>
    <p><span>安全保障</span><span>风控体系</span><span>保护金</span><span>资金托管</span><span>媒体报道</span></p>
  </div>
  <div class="hotline abs"><small>客服电话</small><strong>400-088-2046</strong><em>工作日 9:00 - 18:00</em></div>
  <div class="service-row abs">客户服务：<i></i><i></i><i></i><span class="pill">在线客服</span></div>
  <div class="badges abs"><i></i><i></i><i></i><i></i><i></i></div>
  <p class="copyright abs">Copyright © 2014 Kelumo.cn 版权所有 · 示例备案编号 0000000</p>
  <div class="footer-brand abs"><i></i>Kelumo</div>
</footer>

</body>
</html>
```